Business Card Design

New business card design

Target Market(s)

Residential & Commercial Property Managers

Industry/Entity Type

Plumbing Services

Contact Information for Business Card

Name - Rowan Keddle, title - Director, Phone Number - 0431 286 517, email - rowan@tbk-plumbing.com.au, Company ABN - 73 215 904 386,

Font styles to use
Sans Serif

Colors
0054AA
0677BA
7BADD7
CADEEF
E8F1F8

```html
<!DOCTYPE html>
<html lang="en">
<head>
<meta charset="utf-8">
<title>TBK Plumbing Services – Business Card</title>
<link rel="stylesheet" href="https://fonts.googleapis.com/css2?family=Montserrat:wght@300;400;500;700&display=swap">
<style>
  :root {
    --backdrop: #e9e6e1;
    --card-white: #ffffff;
    --ink: #1c2530;
    --navy: #1c2430;
    --brand-blue: #29a8e0;
    --tagline-front: #8a7b6b;
    --tagline-back: #4a4d52;
    --brand-back: #3a5a8c;
  }
  * { margin: 0; padding: 0; box-sizing: border-box; }
  html, body { width: 900px; height: 1200px; overflow: hidden; }
  body {
    position: relative;
    background: var(--backdrop);
    font-family: "Montserrat", sans-serif;
    color: var(--ink);
  }
  .card {
    position: absolute;
    border-radius: 22px;
    overflow: hidden;
    box-shadow: 0 8px 20px rgba(0,0,0,0.25);
  }
  .card--front { left: 80px; top: 130px; width: 742px; height: 442px; background: var(--card-white); }
  .card--back { left: 78px; top: 638px; width: 744px; height: 442px; background: var(--navy); }

  .brand { position: absolute; text-align: center; }
  .brand__name { display: block; font-weight: 300; line-height: 1; letter-spacing: 4px; }
  .brand__tagline { display: block; font-weight: 300; white-space: nowrap; }

  .card--front .brand { left: 53px; top: 158px; width: 284px; }
  .card--front .brand__name { font-size: 88px; color: var(--ink); }
  .card--front .brand__tagline { margin-top: 20px; font-size: 12px; letter-spacing: 9.4px; color: var(--tagline-front); }

  .divider { position: absolute; left: 367px; top: 138px; width: 2px; height: 182px; background: var(--ink); }

  .contact { position: absolute; left: 388px; top: 126px; }
  .contact__name { font-size: 25px; font-weight: 700; line-height: 1.1; }
  .contact__title { font-size: 15px; font-weight: 400; margin-top: 3px; }
  .contact__list { list-style: none; margin-top: 20px; }
  .contact__item { display: flex; align-items: center; height: 30.5px; font-size: 15.5px; }
  .contact__icon { width: 16px; height: 16px; margin-right: 10px; fill: var(--ink); }
  .contact__abn { font-weight: 700; }

  .band { position: absolute; top: 388px; height: 32px; }
  .band--dark { left: 0; width: 626px; background: var(--ink); }
  .band--blue { left: 690px; width: 52px; background: var(--brand-blue); }
  .band-dot { position: absolute; left: 622px; top: 370px; }

  .card--back .brand { left: 0; top: 168px; width: 744px; }
  .card--back .brand__name { font-size: 140px; color: var(--brand-back); }
  .card--back .brand__tagline { margin-top: 30px; font-size: 17px; letter-spacing: 17px; color: var(--tagline-back); }
</style>
</head>
<body>
  <section class="card card--front" aria-label="Business card front">
    <div class="brand">
      <span class="brand__name">tbk</span>
      <span class="brand__tagline">plumbing services</span>
    </div>
    <div class="divider"></div>
    <div class="contact">
      <p class="contact__name">Rowan Keddle</p>
      <p class="contact__title">Director</p>
      <ul class="contact__list">
        <li class="contact__item">
          <svg class="contact__icon" viewBox="0 0 24 24" aria-hidden="true"><path d="M6.6 10.8c1.4 2.8 3.8 5.1 6.6 6.6l2.2-2.2c.3-.3.7-.4 1-.2 1.1.4 2.3.6 3.6.6.6 0 1 .4 1 1V20c0 .6-.4 1-1 1C10.6 21 3 13.4 3 4c0-.6.4-1 1-1h3.5c.6 0 1 .4 1 1 0 1.3.2 2.5.6 3.6.1.3 0 .7-.2 1l-2.3 2.2z"/></svg>
          0431 286 517
        </li>
        <li class="contact__item">
          <svg class="contact__icon" viewBox="0 0 24 24" aria-hidden="true"><path d="M3 6h18v12H3z M3 6l9 7 9-7" fill="var(--ink)"/><path d="M3.5 6.5l8.5 6.5 8.5-6.5" fill="none" stroke="#fff" stroke-width="1.5"/></svg>
          rowan@tbk-plumbing.com.au
        </li>
        <li class="contact__item">
          <svg class="contact__icon" viewBox="0 0 24 24" aria-hidden="true"><circle cx="12" cy="12" r="9" fill="none" stroke="var(--ink)" stroke-width="2"/><path d="M3 12h18M12 3c3 3 3 15 0 18M12 3c-3 3-3 15 0 18" fill="none" stroke="var(--ink)" stroke-width="1.6"/></svg>
          www.tbk-plumbing.com.au
        </li>
        <li class="contact__item"><span class="contact__abn">ABN</span>&nbsp;- 73 215 904 386</li>
      </ul>
    </div>
    <div class="band band--dark"></div>
    <div class="band band--blue"></div>
    <svg class="band-dot" width="68" height="68" viewBox="0 0 68 68" aria-hidden="true">
      <circle cx="34" cy="34" r="33" fill="var(--card-white)"/>
      <circle cx="34" cy="34" r="24" fill="var(--brand-blue)"/>
    </svg>
  </section>

  <section class="card card--back" aria-label="Business card back">
    <div class="brand">
      <span class="brand__name">tbk</span>
      <span class="brand__tagline">plumbing services</span>
    </div>
  </section>
</body>
</html>
```